My business is Property developing Stationary

I want business card and stationery. Please have the formate so I can edit details on card and stationary.

Please see my logo and on the back of the card I want it same red as my logo and I will provide copy that I want on the back of the card.

Also need an email signature

On the business card and email signature add below copy:
Project Management- Acquisitions- Syndicates- Joint Ventures

Target Market(s)

Property investors

Industry/Entity Type

Business

Requirements
Must have
• Reflect my Logo

```html
<!DOCTYPE html>
<html lang="en">
<head>
<meta charset="utf-8">
<title>Ventura Property Group – Business Card</title>
<link rel="stylesheet" href="https://fonts.googleapis.com/css2?family=Jost:wght@400;500;700&display=swap">
<style>
  :root {
    --stage: #1e1e1f;
    --paper: #f7f7f6;
    --brand-red: #c9302a;
    --ink: #2b2b2b;
    --soft-grey: #e4e4e4;
    --mid-grey: #9a9a9a;
    --deep-red: #8f1f1b;
    --white: #ffffff;
  }
  * { margin: 0; padding: 0; box-sizing: border-box; }
  html, body {
    width: 1200px; height: 1000px; overflow: hidden;
    background: var(--stage);
    font-family: "Jost", "Futura", sans-serif;
  }
  .stage { position: relative; width: 1200px; height: 1000px; }
  .card { position: absolute; width: 580px; height: 324px; overflow: hidden; }
  .card-front { left: 200px; top: 148px; background: var(--paper); }
  .card-back { left: 420px; top: 548px; width: 578px; background: var(--brand-red); }

  .front-band {
    position: absolute; left: 0; bottom: 0; width: 462px; height: 16px;
    background: var(--brand-red);
  }
  .front-decor {
    position: absolute; left: 462px; top: 130px; width: 118px; height: 194px;
    background: linear-gradient(180deg, var(--paper) 0%, var(--soft-grey) 45%, var(--mid-grey) 100%);
  }
  .back-decor {
    position: absolute; left: 0; top: 110px; width: 276px; height: 214px;
    background: linear-gradient(180deg, var(--brand-red) 0%, var(--deep-red) 100%);
  }

  .holder { position: absolute; left: 30px; top: 58px; color: var(--ink); }
  .holder-name { color: var(--brand-red); font-weight: 700; font-size: 18px; letter-spacing: 0.3px; line-height: 22px; }
  .holder-role { font-size: 15px; line-height: 20px; }

  .contact-list { position: absolute; left: 30px; top: 126px; list-style: none; color: var(--ink); font-size: 14px; }
  .contact-list li { display: flex; align-items: center; height: 18px; }
  .contact-icon { width: 13px; height: 13px; margin-right: 10px; flex: none; }

  .address { position: absolute; left: 30px; top: 219px; font-size: 14px; line-height: 17px; color: var(--ink); }
  .services { position: absolute; left: 30px; top: 277px; font-size: 12.5px; color: var(--ink); }

  .brand-name { position: absolute; line-height: 1; text-align: center; font-weight: 700; }
  .brand-name .brand-main { display: block; font-size: 42px; letter-spacing: 1px; }
  .brand-name .brand-sub { display: block; font-size: 16px; margin-top: 4px; }
  .card-front .brand-name { left: 300px; top: 56px; width: 230px; color: var(--brand-red); }
  .card-back .brand-name { left: 270px; top: 74px; width: 255px; color: var(--white); }

  .back-web { position: absolute; right: 54px; top: 266px; color: var(--white); font-size: 14px; letter-spacing: 0.3px; }
</style>
</head>
<body>
<main class="stage">

  <section class="card card-front" aria-label="Business card front">
    <div class="front-decor" role="img" aria-label="Decorative stripe artwork in grey, black and red"></div>
    <div class="front-band"></div>

    <div class="holder">
      <p class="holder-name">MARCO VENTURA</p>
      <p class="holder-role">Managing Director</p>
    </div>

    <ul class="contact-list">
      <li>
        <svg class="contact-icon" viewBox="0 0 13 13" aria-hidden="true"><rect width="13" height="13" rx="2" fill="var(--brand-red)"/><rect x="4" y="2.5" width="5" height="8" rx="1" fill="none" stroke="#fff" stroke-width="1"/></svg>
        +61 (0) 400 123 456
      </li>
      <li>
        <svg class="contact-icon" viewBox="0 0 13 13" aria-hidden="true"><rect width="13" height="13" rx="2" fill="var(--brand-red)"/><path d="M4 3 L5.5 3 L6 5 L5 6 Q6 8 7.5 8.5 L8.5 7.5 L10 8 L10 9.5 Q6 10 3.5 5 Z" fill="#fff"/></svg>
        +61 (0) 400 123 789
      </li>
      <li>
        <svg class="contact-icon" viewBox="0 0 13 13" aria-hidden="true"><rect width="13" height="13" rx="2" fill="var(--brand-red)"/><rect x="2.5" y="3.5" width="8" height="6" fill="none" stroke="#fff" stroke-width="1"/><path d="M2.5 3.5 L6.5 7 L10.5 3.5" fill="none" stroke="#fff" stroke-width="1"/></svg>
        info@venturaproperty.com
      </li>
      <li>
        <svg class="contact-icon" viewBox="0 0 13 13" aria-hidden="true"><rect width="13" height="13" rx="2" fill="var(--brand-red)"/><circle cx="6.5" cy="6.5" r="4" fill="none" stroke="#fff" stroke-width="1"/><path d="M2.5 6.5 H10.5 M6.5 2.5 V10.5" stroke="#fff" stroke-width="0.8"/></svg>
        www.venturaproperty.com
      </li>
    </ul>

    <p class="address">Level 12, Harbour Tower<br>18 Example Street, Sydney</p>
    <p class="services">Project Management - Acquisitions - Syndicates - Joint Ventures</p>

    <p class="brand-name"><span class="brand-main">VENTURA</span><span class="brand-sub">Property Group</span></p>
  </section>

  <section class="card card-back" aria-label="Business card back">
    <div class="back-decor" role="img" aria-label="Decorative stripe artwork in white, black and red"></div>
    <p class="brand-name"><span class="brand-main">VENTURA</span><span class="brand-sub">Property Group</span></p>
    <p class="back-web">www.venturaproperty.com</p>
  </section>

</main>
</body>
</html>
```